Webdesign für freie Trauungen
Zielgruppe
Webseite für Hochzeitspaare, Trauerende, Bestatter, Interessierte
Aufgabenstellung
Internetseite
Briefing:
Onepager
Internetseite soll wirken:
Modern
Schlank
Klar
Vertrauenserweckend
professionell
Home:
Reden für besondere Momente im Leben
Schrift an Flyer anpassen
REDEN.
ERZÄHLEN.
ERINNERN.
BERÜHREN.
Bild von mir,
Dazu, meine Reden sind:
freundlich
authentisch
ehrlich
einfühlsam
taktvoll
humorvoll
tiefsinnig
tröstend
nett
zugewandt
interessant
nach Euren Wünschen
mit Euren Inhalten
individuell
sehr persönlich
kreativ
wortgewandt
erfahren
Sprechen Sie mich an! ?
FREIE TRAUUNG:
EINFACH HIMMLISCH!
eine Liebesgeschichte erzählen
Sich ein Versprechen geben
JA zueinander sagen
Mit lieben Menschen feiern
wo, wann, wie - das entscheidet Ihr!
Segensfeier - Willkommensfeier:
im Leben willkommen heißen
Was bedeutet der Name des Kindes?
Was wollt Ihr Eurem Kind mitgeben?
Was wünscht Ihr Euch für Euer Kind?
TRAUERFEIER:
an schöne Momente erinnern
Einen Menschen mit Worten lebendig werden lassen
Mit einer persönlichen und bewegenden Ansprache
Mit all dem, was Sie sich wünschen!
REDEN ZU GEBURTSTAGEN:
mit Humor, Witz und Verstand gemeinsam zurück schauen
Und von Träumen und Sehnsüchten erzählen
Reden zum Jubiläum:
gemeinsam zurück schauen
Geleistetes würdigen
Veränderungen verständlich machen
Ausblicke wagen
Biographien:
festhalten, damit nichts von Ihrer Lebensgeschichte verloren geht
Sie erinnern sich und ich schreibe auf
Referenzen:
???? Wie am besten ???
Persönliches Vita:
Studium an der Hohen Akademie Tellbrück:
- Publizistik
Germanistik
Volkswirtschaftslehre
Lateinamerikanistik
Abschluß: Magistra Artium
Freie Rednerin seit 1998
Telefonnummer 015923847261
Email: marlies.Kersten@postfeld.de
Wirk..

```html
<!DOCTYPE html>
<html lang="de">
<head>
<meta charset="utf-8">
<title>Kersten Reden – Reden für besondere Momente im Leben</title>
<link rel="stylesheet" href="https://fonts.googleapis.com/css2?family=Source+Sans+3:wght@300;400&family=Alegreya+Sans:wght@400;500;700&display=swap">
<style>
:root{
  --teal:#5f9c98;
  --ink:#4a4a4a;
  --soft:#777;
  --bar:#5a5758;
  --mist:#e9eeed;
  --paper:#f5f5f5;
  --white:#fff;
  --dark:#2f2c2d;
}
*{margin:0;padding:0;box-sizing:border-box}
html,body{width:1200px;height:3188px;overflow:hidden;background:var(--white)}
body{position:relative;font-family:"Alegreya Sans",sans-serif;color:var(--ink)}
.abs{position:absolute}
.topbar{left:0;top:0;width:1200px;height:30px;background:var(--bar);color:var(--white);font-size:11px;font-weight:500;text-align:right;padding:10px 33px 0 0}
.header{left:0;top:30px;width:1200px;height:88px;background:var(--white)}
.brand{left:27px;top:29px;font-family:"Alegreya Sans",sans-serif;font-weight:400;font-size:26px;line-height:30px;color:#222;white-space:nowrap}
.nav{top:41px;font-size:11px;letter-spacing:.3px;color:var(--soft);font-weight:500}
.nav.active{color:var(--teal)}
.photo{display:block}
.kicker{font-size:11px;color:var(--teal);text-transform:uppercase;letter-spacing:.3px}
.headline{font-family:"Source Sans 3",sans-serif;font-weight:300;color:#3e3e3e;text-transform:uppercase}
.band{background:var(--mist)}
.btn{background:var(--teal);color:var(--white);font-size:11px;font-weight:700;border-radius:15px;text-align:center;text-transform:uppercase}
.service h3{font-family:"Source Sans 3",sans-serif;font-weight:400;font-size:17px;line-height:21px;color:#555;text-transform:uppercase;margin-bottom:14px}
.service p{font-size:12px;line-height:15.6px;color:var(--soft)}
.body-text{font-size:13px;line-height:15.5px;color:var(--soft)}
.foot h4{font-size:10px;font-weight:500;color:#444;text-transform:uppercase;margin-bottom:14px}
.foot p{font-size:11px;line-height:15px;color:#888}
</style>
</head>
<body>

<div class="abs topbar">0159-23847261 | marlies.kersten@postfeld.de</div>

<header class="abs header">
  <div class="abs brand">Kersten Reden</div>
  <span class="abs nav active" style="left:693px">STARTSEITE</span>
  <span class="abs nav" style="left:795px">MEINE DIENSTLEISTUNG</span>
  <span class="abs nav" style="left:958px">PERSÖNLICHES VITA</span>
  <span class="abs nav" style="left:1101px">REFERENZEN</span>
</header>

<div class="abs photo" role="img" aria-label="Wiesenblumen mit blauen Kornblumen vor hellem Himmel" style="left:0;top:118px;width:1200px;height:248px;background:linear-gradient(180deg,#d8dde6 0%,#c7ccc9 55%,#a7a68c 100%)"></div>

<section>
  <div class="abs band" style="left:0;top:799px;width:1200px;height:822px"></div>
  <div class="abs kicker" style="left:0;top:426px;width:1200px;text-align:center">Reden für besondere Momente im Leben</div>
  <h1 class="abs headline" style="left:0;top:466px;width:1200px;text-align:center;font-size:38px;line-height:45px">Reden. Erzählen.<br>Erinnern. Berühren.</h1>
  <div class="abs photo" role="img" aria-label="Porträt der Rednerin vor grünem Samtsessel" style="left:287px;top:602px;width:625px;height:417px;background:linear-gradient(90deg,#5a4536 0%,#b9a57c 45%,#2f5a45 80%,#3e6a56 100%)"></div>

  <div class="abs" style="left:287px;top:1092px;font-size:12.5px;font-weight:700;color:#555">Meine Reden sind...</div>
  <p class="abs body-text" style="left:287px;top:1122px;width:630px">freundlich, authentisch, ehrlich, einfühlsam, taktvoll, humorvoll, tiefsinnig, tröstend, nett, zugewandt, interessant, nach Euren Wünschen, mit Euren Inhalten, individuell, sehr persönlich, kreativ, wortgewandt, erfahren</p>
  <div class="abs btn" style="left:287px;top:1180px;width:167px;height:28px;line-height:28px">Sprechen Sie mich an!</div>

  <div class="abs service" style="left:287px;top:1260px;width:190px"><h3>Freie Trauung:<br>Einfach himmlisch!</h3><p>eine Liebesgeschichte erzählen<br>Sich ein Versprechen geben<br>JA zueinander sagen<br>Mit lieben Menschen feiern<br><br>wo, wann, wie – das entscheidet Ihr!</p></div>
  <div class="abs service" style="left:506px;top:1260px;width:190px"><h3>Segensfeier<br>Willkommensfeier</h3><p>im Leben willkommen heißen<br>Was bedeutet der Name des Kindes?<br>Was wollt Ihr Eurem Kind mitgeben?<br>Was wünscht Ihr Euch für Euer Kind?</p></div>
  <div class="abs service" style="left:725px;top:1260px;width:190px"><h3>Trauerfeier<br>&nbsp;</h3><p>an schöne Momente erinnern<br>Einen Menschen mit Worten<br>lebendig werden lassen<br>Mit einer persönlichen und<br>bewegenden Ansprache<br>Mit all dem, was Sie sich wünschen!</p></div>

  <div class="abs service" style="left:287px;top:1452px;width:190px"><h3>Reden zu<br>Geburtstagen</h3><p>mit Humor, Witz und Verstand<br>gemeinsam zurück schauen<br>Und von Träumen und Sehnsüchten<br>erzählen</p></div>
  <div class="abs service" style="left:506px;top:1452px;width:190px"><h3>Reden zum<br>Jubiläum</h3><p>gemeinsam zurück schauen<br>Geleistetes würdigen<br>Veränderungen verständlich machen<br>Ausblicke wagen</p></div>
  <div class="abs service" style="left:725px;top:1452px;width:190px"><h3>Biographien<br>&nbsp;</h3><p>festhalten, damit nichts von Ihrer<br>Lebensgeschichte verloren geht<br>Sie erinnern sich und ich schreibe<br>auf</p></div>
</section>

<section>
  <div class="abs photo" role="img" aria-label="Porträt der Rednerin an einem hellen Tisch" style="left:287px;top:1698px;width:261px;height:368px;background:linear-gradient(180deg,#c9d3cf 0%,#d9c9a3 40%,#3a3a3e 75%,#e6e6e4 100%)"></div>
  <div class="abs kicker" style="left:605px;top:1726px">kerstenreden.de</div>
  <h2 class="abs headline" style="left:605px;top:1757px;font-size:30px">Persönliches Vita</h2>
  <p class="abs body-text" style="left:605px;top:1814px;width:320px">Studium an der Hohen Akademie Tellbrück: Publizistik, Germanistik, Volkswirtschaftslehre, Lateinamerikanistik<br>Abschluß: Magistra Artium</p>
  <div class="abs" style="left:605px;top:1871px;font-size:12.5px;font-weight:700;color:#555">Freie Rednerin seit 1998</div>
  <div class="abs btn" style="left:605px;top:1918px;width:167px;height:28px;line-height:28px">Kontakt aufnehmen</div>
  <div class="abs" style="left:605px;top:1982px;font-size:12.5px;font-weight:700;color:#555">0159-23847261 | marlies.kersten@postfeld.de</div>
  <p class="abs body-text" style="left:605px;top:2007px;width:310px">Wirkungskreis: Aachen, Viersen, Düsseldorf, Krefeld, Erkelenz, Neuss, Köln</p>
</section>

<section>
  <div class="abs" style="left:0;top:2137px;width:1200px;height:418px;background:var(--paper)"></div>
  <div class="abs kicker" style="left:0;top:2200px;width:1200px;text-align:center">Kundenstimmen</div>
  <h2 class="abs headline" style="left:0;top:2236px;width:1200px;text-align:center;font-size:30px">Das sagen Kunden über mich</h2>
  <div class="abs photo" role="img" aria-label="Porträtfoto einer Kundin" style="left:563px;top:2305px;width:74px;height:74px;border-radius:50%;background:radial-gradient(circle at 50% 45%,#d8a98a 0%,#b57a4f 60%,#8a5a3a 100%)"></div>
  <p class="abs body-text" style="left:320px;top:2403px;width:560px;text-align:center">Sed eiusmod tempor incidunt ut labore et dolore magna aliqua. Ut enim ad minim veniam, quis nostrud exercitation ullamco laboris nisi ut aliquid ex ea commodi consequat.</p>
  <div class="abs" style="left:0;top:2442px;width:1200px;text-align:center;font-size:12.5px;font-weight:500;color:#555">Miriam Musterfrau</div>
  <svg class="abs" style="left:576px;top:2478px" width="48" height="12" viewBox="0 0 48 12" aria-hidden="true">
    <circle cx="8" cy="6" r="4.5" fill="var(--teal)"/><circle cx="24" cy="6" r="4.5" fill="#fff"/><circle cx="39" cy="6" r="4.5" fill="#fff"/>
  </svg>
</section>

<div class="abs photo" role="img" aria-label="Blaue Glockenblumen mit Schmetterling vor grünem Hintergrund" style="left:0;top:2561px;width:1200px;height:430px;background:linear-gradient(160deg,#8fb0ae 0%,#c9d8d5 35%,#9aa4c9 60%,#7d9683 100%)"></div>

<footer>
  <div class="abs band" style="left:0;top:2994px;width:1200px;height:194px"></div>
  <div class="abs" style="left:287px;top:3039px;width:72px;height:72px;background:var(--dark)"></div>
  <div class="abs" style="left:376px;top:3039px;font-size:11px;font-weight:500;line-height:20px;color:#333">REDEN.<br>ERZÄHLEN.<br>ERINNERN.<br>BERÜHREN.</div>
  <div class="abs foot" style="left:502px;top:3039px"><h4>Adresse</h4><p>Marlies Kersten<br>Musterstraße 34<br>98765 Musterstadt</p></div>
  <div class="abs foot" style="left:657px;top:3039px"><h4>Kontakt</h4><p>Telefon: 0159-23847261<br>marlies.kersten@postfeld.de<br>kerstenreden.de</p></div>
  <div class="abs foot" style="left:846px;top:3039px"><h4>Rechtliches</h4><p>Impressum<br>Datenschutz</p></div>
  <div class="abs" style="left:0;top:3163px;width:1200px;text-align:center;font-size:9px;color:#666">COPYRIGHT @2021 MARLIES KERSTEN</div>
</footer>

</body>
</html>
```